pathology learning flashcard template graphic design .

Creative designs for 2 sides of the flashcards to include colorful sectioning and font sizes that will make it easy to use in studying.

```html
<!DOCTYPE html>
<html lang="en">
<head>
<meta charset="utf-8">
<title>Pathology Flashcard – Gastrointestinal</title>
<link href="https://fonts.googleapis.com/css2?family=Montserrat:wght@600;700;800&family=Open+Sans:wght@400;600;700&display=swap" rel="stylesheet">
<style>
  :root{
    --bg:#1d5c95;
    --card-top:#ffffff;
    --card-mid:#eef5f9;
    --card-bottom:#cfe3ee;
    --navy:#16477a;
    --blue:#1f6aa5;
    --ink:#1d2630;
    --band:#1c4f85;
    --band-light:#ffffff;
    --art-a:#f2b7b5;
    --art-b:#4a78b0;
    --avatar-a:#e9d8c6;
    --avatar-b:#3a8a5e;
  }
  *{box-sizing:border-box;margin:0;padding:0}
  html,body{width:1200px;height:675px;overflow:hidden}
  body{
    background:radial-gradient(ellipse at 50% 60%,#2a78b8 0%,var(--bg) 55%,#123f6e 100%);
    font-family:"Open Sans",Arial,sans-serif;
    color:var(--ink);
    position:relative;
  }
  .card{
    position:absolute;top:177px;width:560px;height:320px;
    background:linear-gradient(180deg,var(--card-top) 0%,var(--card-mid) 45%,var(--card-bottom) 100%);
    border-radius:4px;
    box-shadow:0 14px 30px rgba(0,0,0,.35);
    overflow:hidden;
  }
  .card--front{left:26px}
  .card--back{left:614px}
  .card__art{
    position:absolute;top:14px;right:22px;width:70px;height:62px;border-radius:8px;
    background:linear-gradient(135deg,var(--art-b) 0%,var(--art-a) 70%);
    opacity:.85;
  }
  .card__title{
    position:absolute;top:34px;left:0;right:0;text-align:center;
    font-family:"Montserrat",Arial,sans-serif;font-weight:800;
    color:var(--navy);letter-spacing:2px;font-size:17px;
  }
  .ribbon{position:absolute;left:0;top:74px;height:26px}
  .ribbon svg{position:absolute;left:0;top:0}
  .ribbon__text{
    position:relative;display:block;padding:0 0 0 16px;line-height:26px;
    font-family:"Montserrat",Arial,sans-serif;font-weight:700;font-size:12.5px;color:var(--band-light);
  }
  .avatar{
    position:absolute;left:22px;top:150px;width:80px;height:80px;border-radius:6px;
    border:3px solid var(--navy);
    background:linear-gradient(180deg,var(--avatar-a) 0%,var(--avatar-a) 55%,var(--avatar-b) 100%);
  }
  .case__text{
    position:absolute;left:118px;top:116px;width:420px;
    font-size:9.6px;line-height:1.45;
  }
  .case__options{
    position:absolute;left:118px;top:240px;width:420px;
    font-weight:700;font-size:10.5px;color:var(--ink);word-spacing:1px;
  }
  .back__body{position:absolute;left:24px;top:70px;width:512px;font-size:9.4px;line-height:1.4}
  .section__head{
    font-family:"Montserrat",Arial,sans-serif;font-weight:700;color:var(--blue);
    font-size:10.5px;margin-top:4px;
  }
  .section__list{list-style:none}
  .section__list li{padding-left:9px;position:relative;font-weight:600}
  .section__list li::before{content:"";position:absolute;left:1px;top:5px;width:4px;height:4px;border-radius:50%;background:var(--ink)}
  .answer{position:absolute;left:0;top:204px;height:26px}
  .answer svg{position:absolute;left:0;top:0}
  .answer__text{
    position:relative;display:block;padding-left:24px;line-height:26px;
    font-family:"Montserrat",Arial,sans-serif;font-weight:700;font-size:13px;color:var(--band-light);
  }
  .explanation{position:absolute;left:24px;top:238px;width:512px;font-size:9.4px;line-height:1.45;font-weight:600}
</style>
</head>
<body>

<section class="card card--front" aria-label="Flashcard front: case question">
  <div class="card__art" role="img" aria-label="Illustration of a stomach and esophagus with a magnifying glass"></div>
  <h1 class="card__title">GASTROINTESTINAL</h1>
  <div class="ribbon">
    <svg width="210" height="26" viewBox="0 0 210 26" aria-hidden="true"><polygon points="0,0 210,0 198,26 0,26" fill="#1c4f85"/></svg>
    <span class="ribbon__text">Pathology Case ID 0001</span>
  </div>
  <div class="avatar" role="img" aria-label="Illustration of an elderly woman patient"></div>
  <p class="case__text">50-year-old woman comes to the clinic because she has difficulty swallowing for the past few months. She says symptoms have been worsening. She also complains of cough, mostly at night and in fear of choking, has stopped eating many foods, losing about 12 lbs in the past 3 months. Past medical history is unremarkable. Vital signs are normal and physical exam is unremarkable. Chest x-ray with demonstrates an air-fluid level, while manometry shows absent relaxation of the lower esophageal sphincter during swallowing. What is the most likely diagnosis?</p>
  <p class="case__options">A) GERD , B) Barret Esophagus , C) Achalasia , D) Eosinophilic esophagitis</p>
</section>

<section class="card card--back" aria-label="Flashcard back: answer and explanation">
  <div class="card__art" role="img" aria-label="Illustration of a stomach and esophagus with a magnifying glass"></div>
  <h2 class="card__title">ACHALASIA</h2>
  <div class="back__body">
    <h3 class="section__head">Definition:</h3>
    <ul class="section__list"><li>Motility disorder where esophageal relaxation is impaired in the lower esophageal sphincter (LES).</li></ul>
    <h3 class="section__head">Etiology/Pathology:</h3>
    <ul class="section__list">
      <li>Destruction of inhibitory neurons in the Auerbach plexus.</li>
      <li>Loss of peristalsis in the lower esophageal sphincter (Lower-two thirds of the esophagus).</li>
    </ul>
    <h3 class="section__head">P/E and Symptoms:</h3>
    <ul class="section__list"><li>Dysphagia that is progressive, regurgitation, weight-loss, dry cough, chest pain, GERD, esophageal perforation, squamous cell carcinoma, aspiration pneumonia.</li></ul>
  </div>
  <div class="answer">
    <svg width="190" height="26" viewBox="0 0 190 26" aria-hidden="true"><polygon points="0,0 190,0 180,26 0,26" fill="#1c4f85"/></svg>
    <span class="answer__text">C - Achalasia</span>
  </div>
  <p class="explanation">Symptoms and studies suggestive of achalasia. Patient's manometry presents with no relaxation of the lower esophageal sphincter during swallowing. Patient also complains of dysphagia and is unable to swallow properly, leading to weight loss. Patient has no past infection or inflammation, ruling out eosinophilic esophagitis. Patient does not have chronic GERD, eliminating the possibility of Barrett esophagus, in which at least 5 years of acid reflux are beforehand to develop columnar metaplasia.</p>
</section>

</body>
</html>
```